New Business Card Design Project LORVANTI-Italy

we are LORVANTI-Italy
our company in the market for 3 years we are luxury cosmetic company and its about time for a facelift :)
i will like to have elegant luxurious and unique business card
that will give the person that get it a unique, luxurious and elegant impression
I'm VERY OPEN FOR NEW IDEAS , even duo i add a few files of things that i see on line and i like them

i add my logo as well
my website is LORVANTI.COM
(if you would like to see the main style that we have)

Target Market(s)

adult that have money :)

Industry/Entity Type

Business

Contact Information for Business Card

Name - Dario Lorvanti
Position - CEO and CO Founder
address - 4817 E Halvern
telephone - 555-384-1926
email - dario@lorvanti.com
fax - 555-384-1926
website - LORVANTI.COM

Colors
000000
959595
fbee3e
ffffff

Requirements
Must have
• big logo in GOLD color
• elegant look
• impressive
Nice to have
• not must but maybe classy pattern background
• not must but maybe emblem
• maybe clear plastic business card
Should not have
• colors
• images

```html
<!DOCTYPE html>
<html lang="en">
<head>
<meta charset="utf-8">
<title>LORVANTI-Italy Business Card</title>
<link href="https://fonts.googleapis.com/css2?family=Crimson+Text:wght@400;600&display=swap" rel="stylesheet">
<style>
  :root {
    --backdrop: #2a2a2a;
    --card: #040607;
    --gold: #d4a93a;
    --white: #ffffff;
  }
  html, body {
    margin: 0;
    padding: 0;
    width: 1200px;
    height: 864px;
    overflow: hidden;
    background: var(--backdrop);
    font-family: "Crimson Text", Georgia, serif;
  }
  .card {
    position: absolute;
    width: 492px;
    height: 282px;
    background: var(--card);
    box-shadow: 0 6px 14px rgba(0,0,0,.55);
  }
  .card-front { left: 99px; top: 292px; }
  .card-back { left: 608px; top: 292px; }

  .front-mark {
    position: absolute;
    left: 0; right: 0; top: 76px;
    display: flex;
    flex-direction: column;
    align-items: center;
    gap: 14px;
  }
  .mark-ring {
    width: 64px; height: 64px;
    border: 2px solid var(--gold);
    border-radius: 50%;
    box-sizing: border-box;
  }
  .brand-name {
    color: var(--gold);
    font-weight: 400;
    letter-spacing: 1px;
    line-height: 1;
  }
  .front-mark .brand-name { font-size: 30px; }

  .back-mark {
    position: absolute;
    left: 32px; width: 220px; top: 76px;
    display: flex;
    flex-direction: column;
    align-items: center;
    gap: 16px;
  }
  .back-mark .mark-ring { width: 60px; height: 60px; }
  .back-mark .brand-name { font-size: 31px; }

  .divider {
    position: absolute;
    left: 261px; top: 57px;
    width: 1px; height: 167px;
    background: var(--gold);
  }

  .contact {
    position: absolute;
    left: 297px;
    top: 0;
    color: var(--white);
    line-height: 1;
  }
  .contact > * { position: absolute; left: 0; white-space: nowrap; margin: 0; }
  .person-name { top: 53px; font-size: 21px; font-weight: 600; color: var(--gold); }
  .person-role { top: 78px; font-size: 14px; }
  .company { top: 108px; font-size: 14px; font-weight: 600; color: var(--gold); }
  .address { top: 127px; font-size: 14px; }
  .line { font-size: 14px; display: flex; align-items: center; gap: 5px; }
  .line svg { width: 12px; height: 12px; fill: var(--gold); flex: none; }
  .line-phone { top: 157px; }
  .line-fax { top: 175px; }
  .line-email { top: 193px; }
  .line-web { top: 211px; }
</style>
</head>
<body>
  <section class="card card-front" aria-label="Card front">
    <div class="front-mark">
      <div class="mark-ring"></div>
      <div class="brand-name">LORVANTI</div>
    </div>
  </section>

  <section class="card card-back" aria-label="Card back">
    <div class="back-mark">
      <div class="mark-ring"></div>
      <div class="brand-name">LORVANTI</div>
    </div>

    <div class="divider"></div>

    <div class="contact">
      <p class="person-name">Dario Lorvanti</p>
      <p class="person-role">CEO and CO Founder</p>
      <p class="company">LORVANTI-Italy</p>
      <p class="address">4817 E Halvern</p>

      <p class="line line-phone">
        <svg viewBox="0 0 12 12" aria-hidden="true"><path d="M2 1.5c.6-.6 1.3-.5 1.7.1l1 1.4c.3.5.2 1-.2 1.4l-.6.5c.5 1.2 1.3 2 2.5 2.6l.5-.6c.4-.4 1-.5 1.4-.2l1.4 1c.6.4.7 1.1.1 1.7C8.5 11 6.8 10.6 4.5 8.3 2.2 6 1 3.3 2 1.5z"/></svg>
        555-384-1926
      </p>
      <p class="line line-fax">
        <svg viewBox="0 0 12 12" aria-hidden="true"><rect x="3" y="1" width="6" height="3"/><rect x="1" y="4.5" width="10" height="4.5" rx="1"/><rect x="3" y="8" width="6" height="3"/></svg>
        555-384-1926
      </p>
      <p class="line line-email">
        <svg viewBox="0 0 12 12" aria-hidden="true"><path d="M1 3h10v6H1z M1 3l5 3.5L11 3" fill="none" stroke="#d4a93a" stroke-width="1.2"/></svg>
        dario@lorvanti.com
      </p>
      <p class="line line-web">
        <svg viewBox="0 0 12 12" aria-hidden="true"><g fill="none" stroke="#d4a93a" stroke-width="1"><circle cx="6" cy="6" r="5"/><ellipse cx="6" cy="6" rx="2.2" ry="5"/><path d="M1 6h10M2 3.5h8M2 8.5h8"/></g></svg>
        LORVANTI.COM
      </p>
    </div>
  </section>
</body>
</html>
```